Social Media App Needs PPT Template

We need a PowerPoint template for a new social media company based in the DC area called "Bold Ledger." We provide an interactive digital platform for executives to share actionable advice. We would like to see designs that use our orange logo color as an accent, but are mainly grey, white, and black. The final design should communicate clean, chic, modern, and professional.

Target Market(s)

Executives

Industry/Entity Type

Information Technology

Font styles to use
Sans Serif

Colors
f78f20
fbe7d2
ffffff
000000
e8e8e8
757575

Requirements
Must have
• My project must have title page and many options for the body of the ppt (graphs, tables, etc). It also needs to be easy to modify. I must have someone who is experienced in creating powerpoint templates.
Nice to have
• It would be nice to have a very modern and clean design that includes the logo on every page, but still leaves a lot of room for the content of the slide
Should not have
• My design project should not look to busy.

```html
<!DOCTYPE html>
<html lang="en">
<head>
<meta charset="utf-8">
<title>Bold Ledger – About Our Company</title>
<link href="https://fonts.googleapis.com/css2?family=Lato:wght@300;400;700&display=swap" rel="stylesheet">
<style>
  :root {
    --board: #929292;
    --orange: #ee8c1f;
    --orange-deep: #e7821a;
    --charcoal: #474747;
    --slate: #58585a;
    --silver: #cbcbcb;
    --ink: #4a4a4a;
    --body-text: #7a7a7a;
    --white: #ffffff;
    --footer-text: #dddddd;
  }
  html, body {
    margin: 0;
    padding: 0;
    width: 1200px;
    height: 960px;
    overflow: hidden;
    background: var(--board);
    font-family: "Lato", sans-serif;
  }
  .page-label {
    position: absolute;
    top: 44px;
    left: 0;
    width: 1200px;
    text-align: center;
    font-weight: 300;
    font-size: 24px;
    color: #f4f4f4;
    margin: 0;
  }
  .slide {
    position: absolute;
    left: 87px;
    top: 128px;
    width: 1046px;
    height: 784px;
    display: block;
  }
  .slide-title { font-family: "Lato", sans-serif; font-weight: 300; font-size: 50px; fill: var(--white); }
  .brand-name { font-family: "Lato", sans-serif; font-weight: 700; font-size: 30px; fill: var(--white); }
  .section-heading { font-family: "Lato", sans-serif; font-weight: 700; font-size: 30px; }
  .heading-dark { fill: var(--ink); }
  .heading-orange { fill: var(--orange); }
  .heading-silver { fill: var(--silver); }
  .section-body { font-family: "Lato", sans-serif; font-weight: 400; font-size: 22px; fill: var(--body-text); }
  .share-label { font-family: "Lato", sans-serif; font-weight: 400; font-size: 26px; fill: var(--white); text-anchor: middle; }
  .footer-text { font-family: "Lato", sans-serif; font-weight: 400; font-size: 18px; fill: var(--footer-text); }
</style>
</head>
<body>
  <p class="page-label">Page 8</p>

  <svg class="slide" viewBox="0 0 1307 980" xmlns="http://www.w3.org/2000/svg" aria-label="About Our Company slide">
    <defs>
      <radialGradient id="slide-bg" cx="0.55" cy="0.3" r="0.8">
        <stop offset="0" stop-color="#ffffff"/>
        <stop offset="1" stop-color="#efefef"/>
      </radialGradient>
      <linearGradient id="header-band" x1="0" y1="0" x2="1" y2="0">
        <stop offset="0" stop-color="#e8821a"/>
        <stop offset="1" stop-color="#f09424"/>
      </linearGradient>
    </defs>

    <!-- background -->
    <rect class="slide-surface" width="1307" height="980" fill="url(#slide-bg)"/>

    <!-- header -->
    <g class="header">
      <polygon points="1009,43 1307,43 1307,55 997,55" fill="var(--orange)"/>
      <polygon points="0,61 991,61 884,163 0,163" fill="url(#header-band)"/>
      <polygon points="790,61 991,61 930,120 730,120" fill="#f09a2e" opacity="0.35"/>
      <polygon points="1001,61 1307,61 1307,163 891,163" fill="var(--charcoal)"/>
      <polygon points="0,170 879,170 868,181 0,181" fill="var(--charcoal)"/>
      <text class="slide-title" x="40" y="135">About Our Company</text>
      <circle cx="1078" cy="112" r="11" fill="var(--orange)"/>
      <text class="brand-name" x="1098" y="123">Bold Ledger</text>
    </g>

    <!-- donut chart -->
    <g class="share-chart" transform="translate(644,536)">
      <path d="M0,-147 A147,147 0 0 1 147,0 L68,0 A68,68 0 0 0 0,-68 Z" fill="var(--orange)"/>
      <path d="M147,0 A147,147 0 0 1 0,147 L0,68 A68,68 0 0 0 68,0 Z" fill="var(--silver)"/>
      <path d="M0,147 A147,147 0 0 1 -147,0 L-68,0 A68,68 0 0 0 0,68 Z" fill="var(--charcoal)"/>
      <path d="M-147,0 A147,147 0 0 1 0,-147 L0,-68 A68,68 0 0 0 -68,0 Z" fill="var(--slate)"/>
      <line x1="-150" y1="0" x2="150" y2="0" stroke="#ffffff" stroke-width="1.5"/>
      <line x1="0" y1="-150" x2="0" y2="150" stroke="#ffffff" stroke-width="1.5"/>
      <text class="share-label" x="-72" y="-62">25%</text>
      <text class="share-label" x="77" y="-62">25%</text>
      <text class="share-label" x="-72" y="87">25%</text>
      <text class="share-label" x="77" y="87">25%</text>
    </g>

    <!-- leader lines -->
    <g class="leader-lines" fill="none" stroke-width="2">
      <polyline points="109,323 485,323 561,415" stroke="var(--ink)"/>
      <polyline points="726,412 802,324 1174,324" stroke="var(--orange)"/>
      <polyline points="102,654 475,654 523,597" stroke="var(--ink)"/>
      <polyline points="767,615 813,654 1186,654" stroke="var(--silver)"/>
    </g>

    <!-- top-left callout -->
    <g class="callout">
      <text class="section-heading heading-dark" x="109" y="312">NOBIS VIDENTUR</text>
      <text class="section-body" x="109" y="360">Lorem ipsum dolor sit amet,</text>
      <text class="section-body" x="109" y="391.5">consectetuer adipi scing elit,</text>
      <text class="section-body" x="109" y="423">sed diam nonummy nibh</text>
      <text class="section-body" x="109" y="454.5">euismod tin.</text>
    </g>

    <!-- top-right callout -->
    <g class="callout">
      <text class="section-heading heading-orange" x="861" y="312">NOBIS VIDENTUR</text>
      <text class="section-body" x="865" y="360">Lorem ipsum dolor sit amet,</text>
      <text class="section-body" x="865" y="391.5">consectetuer adipi scing elit,</text>
      <text class="section-body" x="865" y="423">sed diam nonummy nibh</text>
      <text class="section-body" x="865" y="454.5">euismod tin.</text>
    </g>

    <!-- bottom-left callout -->
    <g class="callout">
      <text class="section-heading heading-dark" x="109" y="643">NOBIS VIDENTUR</text>
      <text class="section-body" x="109" y="689">Lorem ipsum dolor sit amet,</text>
      <text class="section-body" x="109" y="720.5">consectetuer adipi scing elit,</text>
      <text class="section-body" x="109" y="752">sed diam nonummy nibh</text>
      <text class="section-body" x="109" y="783.5">euismod tin.</text>
    </g>

    <!-- bottom-right callout -->
    <g class="callout">
      <text class="section-heading heading-silver" x="878" y="643">NOBIS VIDENTUR</text>
      <text class="section-body" x="878" y="689">Lorem ipsum dolor sit amet,</text>
      <text class="section-body" x="878" y="720.5">consectetuer adipi scing elit,</text>
      <text class="section-body" x="878" y="752">sed diam nonummy nibh</text>
      <text class="section-body" x="878" y="783.5">euismod tin.</text>
    </g>

    <!-- footer -->
    <g class="footer">
      <polygon points="0,928 375,928 334,966 0,966" fill="var(--charcoal)"/>
      <polygon points="381,928 1307,928 1307,966 341,966" fill="var(--orange-deep)"/>
      <text class="footer-text" x="35" y="953">www.boldledger.com  |  Page 6</text>
    </g>
  </svg>
</body>
</html>
```